Tradlo - Forex Signal Services Moments Matter Most. Reshape your path.

I need an attractive eye catching web design that is azure friendly. I currently have a web programmer working on the backend of my website. Now I need a professional design to attract and retain customers. This site needs to be mobile friendly.

Tradlo is a highly reputable, trustworthy and professional site that offers forex signals to traders in all parts of the globe. With accurate and reliable forex signals, traders can not only make money but also boost their profits.

At Tradlo, we want our clients to have complete faith on us and our services! We also do not want our users to lead a simple and monotonous life. Instead our goal is to help them create an extra source of steady income. However, this is possible only when our clients resolve to change their lives for the better. They need to change their mindset and most importantly develop a positive frame of mind. That’s exactly why at Tradlo, we provide our clients with innumerable personal development tools and resources that’ll aid them in changing all the aspects of their lives. We want our traders to feel inspired and educate them in the right way!

Colors are flexible.

I do like the simplicity of www.brightmarkvo.example.
I do want a design more professional in appearance and not everything on page one.

I have not been able to decide on a logo. There is one of lower quality as I have not paid for it yet but I will if you decide it's the best for my business I will. Or should one feel that they have a better idea for a logo, I will pay for it if i like it.

I have included some of the content of my site so you can get a feel for where I am coming from.
(Please note that this content is still in the editing process)
Updates

Project Deadline Extended Reason: My content was not complete nor finalization of the final logo. We will allow a few more days for designers to modify the website.Thank you for your patience and understanding. Added Tuesday, January 24, 2017

Target Market(s)

I work with Forex Traders, Investors wanting to control their own portfolios, and remote nomads/mellienials

Coding

Coded - Design and coding required

Number of Pages Required

5+ page

Requirements
Must have
• I must have a professional clean look. I want the site to be interactive and eye catching. I want my audience hooked within seconds of opening it. It has to have all important information first. Photos must be legit and not spammy. I work as a representative in the financial market. I want my site to reflect that I stand by my product and reputation means everything to me. This site has to be engaging.
• Sorry, I should have included this earlier of what I will all need on this site.
• I'll have about Tradlo (my company, what we stand for, who we work with, my strategy, etc....
• about me (why i started this company, who I am)
• Performance (graphs and recent posts of signals)
• Membership (how to sign up)
• Terms of service/legal/disclaimers
• FAQS
• Personal Development Resources
• Forex Education Resources
Nice to have
• Quick links to bounce around the site faster.
Should not have
• I do not want over the top white collar conservative.

```html
<!DOCTYPE html>
<html lang="en">
<head>
<meta charset="utf-8">
<title>Tradlo - Forex Signal Services</title>
<link rel="stylesheet" href="https://fonts.googleapis.com/css2?family=Oswald:wght@400;500;600&family=Roboto:wght@300;400;500;700&family=Roboto+Condensed:wght@400;700&display=swap">
<style>
:root{
  --blue:#1f7be0;
  --blue-deep:#1560c2;
  --sky:#3fa0ef;
  --orange:#e06a4a;
  --green:#6cb86a;
  --ink:#2b2f36;
  --text:#3d4450;
  --white:#ffffff;
  --night:#101722;
  --night-2:#1b2535;
  --line:#c8ced6;
}
*{box-sizing:border-box;margin:0;padding:0}
html,body{width:1200px;height:2635px;overflow:hidden}
body{position:relative;background:var(--white);font-family:"Roboto",Arial,sans-serif;color:var(--text)}
.abs{position:absolute}

/* header */
.site-header{position:absolute;left:225px;top:0;width:750px;height:65px;background:var(--white);z-index:5}
.brand{position:absolute;left:0;top:0;width:132px;height:65px;background:#0d0f12;display:flex;align-items:center;justify-content:center;gap:8px}
.brand-dot{width:14px;height:14px;border-radius:50%;background:var(--sky)}
.brand-name{font-family:"Roboto",sans-serif;font-weight:500;font-size:22px;color:var(--white)}
.topline{position:absolute;left:140px;top:5px;font-size:8px;color:#666}
.top-social{position:absolute;right:30px;top:5px;display:flex;gap:8px}
.top-social span{width:14px;height:14px;background:#5a6a80;border-radius:2px}
.top-social span:first-child{background:var(--blue-deep)}
.main-nav{position:absolute;left:225px;top:42px;display:flex;gap:20px;font-family:"Roboto Condensed",sans-serif;font-size:10px;color:#333;letter-spacing:.3px}
.main-nav a{color:inherit;text-decoration:none;padding-bottom:6px}
.main-nav a.active{color:var(--blue);border-bottom:2px solid var(--blue)}
.nav-search{position:absolute;right:12px;top:42px}

/* hero */
.hero{position:absolute;left:0;top:0;width:1200px;height:600px;background:radial-gradient(ellipse at 45% 40%,#9fd2f2 0%,#4c8fc0 35%,#2a5886 65%,#1a3558 100%)}
.hero-band{position:absolute;left:0;top:232px;width:1200px;height:95px;background:rgba(30,70,120,.35)}
.hero-arrow{position:absolute;top:276px;width:62px;height:58px;background:rgba(255,255,255,.85);display:flex;align-items:center;justify-content:center}
.hero-title{position:absolute;left:0;width:1200px;top:236px;text-align:center;font-family:"Oswald",sans-serif;font-weight:600;font-size:60px;letter-spacing:3px;color:var(--white);line-height:1}
.hero-sub{position:absolute;left:0;width:1200px;top:292px;text-align:center;font-family:"Oswald",sans-serif;font-size:22px;letter-spacing:17px;color:var(--white)}
.hero-text{position:absolute;left:380px;width:440px;top:318px;text-align:center;font-family:"Roboto Condensed",sans-serif;font-size:13px;line-height:17px;color:var(--white)}

/* feature boxes */
.features{position:absolute;left:216px;top:513px;width:768px;height:185px;display:flex;z-index:3}
.feature{flex:1;text-align:center;color:var(--white);padding:20px 22px 0}
.feature.orange{background:var(--orange)}
.feature.green{background:var(--green)}
.feature.blue{background:var(--blue)}
.feature h3{font-family:"Oswald",sans-serif;font-weight:400;font-size:20px;letter-spacing:1px;margin:14px 0 10px}
.feature p{font-size:9.5px;font-weight:700;line-height:13px}

/* welcome */
.welcome-bg{position:absolute;left:0;top:600px;width:1200px;height:530px;background:linear-gradient(180deg,#f4f6f9 0%,#e9eef4 60%,#f1f4f8 100%)}
.welcome{position:absolute;left:240px;width:720px;top:725px;text-align:center}
.welcome h2{font-family:"Roboto",sans-serif;font-weight:400;font-size:38px;letter-spacing:5px;color:var(--blue)}
.tagline{font-family:"Roboto Condensed",sans-serif;font-size:19px;letter-spacing:1.5px;color:var(--orange);margin-top:2px}
.tagline-2{font-family:"Roboto Condensed",sans-serif;font-size:18px;letter-spacing:1.5px;color:var(--blue)}
.welcome p{font-size:11.5px;line-height:15px;color:var(--ink);margin-top:16px}
.welcome h4{font-family:"Roboto Condensed",sans-serif;font-weight:700;font-size:16px;letter-spacing:1px;color:var(--blue);margin-top:22px}
.welcome p.tight{margin-top:10px}

/* membership */
.plans-bg{position:absolute;left:0;top:1130px;width:1200px;height:464px;background:linear-gradient(160deg,#2a86e4 0%,#1b6fd4 50%,#1f7ee0 100%)}
.plans{position:absolute;left:260px;width:680px;top:1160px;text-align:center;color:var(--white)}
.plans h2{font-family:"Roboto",sans-serif;font-weight:300;font-size:40px;letter-spacing:7px}
.plans p{font-size:11.5px;line-height:15px;margin-top:12px}
.plan{position:absolute;top:1405px;width:226px;height:264px;background:var(--white);box-shadow:0 2px 6px rgba(0,0,0,.25);text-align:center;z-index:3}
.plan-price{height:44px;background:var(--orange);color:var(--white);font-family:"Roboto Condensed",sans-serif;font-size:21px;letter-spacing:2px;line-height:44px}
.plan-term{height:27px;background:var(--green);color:var(--white);font-family:"Roboto Condensed",sans-serif;font-size:13px;letter-spacing:3px;line-height:27px}
.plan-cta{font-size:14px;color:#888;margin-top:16px;line-height:17px}
.plan-btn{display:inline-block;margin-top:12px;width:112px;height:29px;line-height:29px;background:var(--blue);color:var(--white);font-size:11px;letter-spacing:1px}
.pay-name{font-family:"Roboto",sans-serif;font-weight:700;font-size:15px;color:var(--blue-deep);margin-top:14px}
.pay-btn{width:54px;height:12px;border-radius:6px;background:#f2c14a;margin:3px auto 0}
.pay-cards{display:flex;gap:2px;justify-content:center;margin-top:2px}
.pay-cards span{width:13px;height:8px;background:#9aa5b4}

/* faq */
.faq-bg{position:absolute;left:0;top:1594px;width:1200px;height:520px;background:linear-gradient(180deg,#eaf1f8 0%,#d9e6f2 100%)}
.faq-title{position:absolute;left:0;width:1200px;top:1700px;text-align:center;font-family:"Roboto",sans-serif;font-size:30px;letter-spacing:12px;color:var(--blue)}
.faq-item{position:absolute;width:342px;height:36px;border-bottom:1px solid #55606e;display:flex;align-items:center;gap:14px;font-size:10.5px;font-weight:500;color:#2a3140}
.faq-item i{display:inline-flex;width:12px;height:12px;background:#1b1f26;color:#fff;font-style:normal;font-size:11px;line-height:12px;justify-content:center}
.faq-open{position:absolute;left:234px;top:1782px;width:342px}
.faq-open .q{display:flex;gap:10px;align-items:center;font-size:10.5px;color:var(--blue)}
.faq-open .q i{display:inline-flex;width:15px;height:15px;background:var(--blue);color:#fff;font-style:normal;font-size:11px;justify-content:center;align-items:center}
.faq-open p{font-size:8px;line-height:11px;color:#333;margin-top:10px}

/* contact */
.contact-bg{position:absolute;left:0;top:2114px;width:1200px;height:478px;background:linear-gradient(180deg,var(--night) 0%,var(--night-2) 55%,#0d131c 100%)}
.contact-title{position:absolute;left:0;width:1200px;top:2164px;text-align:center;font-family:"Oswald",sans-serif;font-size:26px;letter-spacing:6px;color:var(--white)}
.contact-rule{position:absolute;left:570px;top:2207px;width:60px;height:2px;background:var(--blue)}
.contact-intro{position:absolute;left:239px;top:2254px;width:220px;font-size:10px;line-height:13px;color:var(--white)}
.contact-phone{position:absolute;left:239px;top:2316px;font-family:"Roboto",sans-serif;font-weight:500;font-size:27px;color:var(--sky);letter-spacing:1px}
.stay{position:absolute;left:239px;top:2382px;font-family:"Oswald",sans-serif;font-size:14px;letter-spacing:3px;color:var(--white)}
.social{position:absolute;left:234px;top:2405px;display:flex;gap:5px}
.social span{width:48px;height:48px;border-radius:10px}
.field{position:absolute;height:34px;background:#1a2230;border-top:2px solid var(--blue);font-size:9px;letter-spacing:1px;color:#c7ccd4;padding:8px 22px}
.send{position:absolute;left:859px;top:2509px;width:106px;height:28px;background:var(--blue);color:var(--white);font-size:10px;letter-spacing:2px;text-align:center;line-height:28px}
.remote{position:absolute;left:234px;top:2500px;width:351px;height:37px;border:1px solid var(--blue);display:flex;align-items:center}
.remote-brand{width:96px;height:100%;background:#ffffff;display:flex;align-items:center;justify-content:center;gap:5px;font-size:10px;font-weight:500;color:var(--blue-deep)}
.remote-brand span{width:10px;height:10px;background:var(--blue)}
.remote p{font-size:8.5px;line-height:11px;color:var(--white);padding:0 10px}
.footer-links{position:absolute;left:360px;top:2560px;width:500px;display:grid;grid-template-columns:repeat(5,1fr);font-size:9.5px;letter-spacing:1px;color:var(--white);text-align:center;line-height:11px}
.bottom-bar{position:absolute;left:0;top:2592px;width:1200px;height:43px;background:var(--blue)}
.copyright{position:absolute;left:240px;top:2602px;font-size:8.5px;letter-spacing:.5px;color:var(--white)}
.back-top{position:absolute;left:885px;top:2605px;font-size:9px;letter-spacing:1px;color:var(--white)}
</style>
</head>
<body>

<section class="hero" role="img" aria-label="Photo of a businessman holding a smartphone surrounded by glowing digital trading graphics and a large FOREX word"></section>
<div class="hero-band"></div>
<div class="hero-arrow" style="left:0"><svg width="14" height="20" viewBox="0 0 14 20"><path d="M11 2 3 10l8 8" fill="none" stroke="#333" stroke-width="2"/></svg></div>
<div class="hero-arrow" style="right:0"><svg width="14" height="20" viewBox="0 0 14 20"><path d="M3 2l8 8-8 8" fill="none" stroke="#333" stroke-width="2"/></svg></div>
<h1 class="hero-title">FOREX SIGNAL</h1>
<div class="hero-sub">SERVICES</div>
<p class="hero-text">Tradlo.com works with both day as well as intraday traders. We only hold a maximum of one position at any given point in time. Once we've placed an order we do not move SL or TP targets.</p>

<header class="site-header">
  <div class="brand"><span class="brand-dot"></span><span class="brand-name">Tradlo</span></div>
  <div class="topline">Make an Appointment | Call : 555-014-2290</div>
  <div class="top-social"><span></span><span></span><span></span><span></span></div>
  <nav class="main-nav">
    <a class="active">HOME</a><a>ABOUT US</a><a>MEMBERSHIP PLANS</a><a>PERFORMANCE</a><a>FAQ</a><a>FOREX RESOURCES</a><a>CONTACT</a>
  </nav>
  <svg class="nav-search" width="11" height="11" viewBox="0 0 11 11"><circle cx="4.5" cy="4.5" r="3.5" fill="none" stroke="#555" stroke-width="1.4"/><path d="M7 7l3.5 3.5" stroke="#555" stroke-width="1.4"/></svg>
</header>

<section class="features">
  <div class="feature orange">
    <svg width="46" height="40" viewBox="0 0 46 40"><g fill="none" stroke="#fff" stroke-width="4"><circle cx="16" cy="22" r="8"/><circle cx="35" cy="10" r="5"/></g><g stroke="#fff" stroke-width="4"><path d="M16 8v5M16 31v5M2 22h5M25 22h5M6 12l4 4M22 28l4 4M26 12l-4 4M10 28l-4 4M35 1v3M35 16v3M26 10h3M41 10h3"/></g></svg>
    <h3>THE TRADLO ADVANTAGE</h3>
    <p>Delivering high-probability forex signals to help you beat the market. Accurate and reliable forex signals to take your trading</p>
  </div>
  <div class="feature green">
    <svg width="44" height="40" viewBox="0 0 44 40"><g fill="#fff"><rect x="4" y="28" width="6" height="10"/><rect x="14" y="22" width="6" height="16"/><rect x="24" y="18" width="6" height="20"/><rect x="34" y="12" width="6" height="26"/></g><path d="M3 22 15 12l8 5L38 4" fill="none" stroke="#fff" stroke-width="3"/><path d="M32 3h7v7" fill="none" stroke="#fff" stroke-width="3"/></svg>
    <h3>TRADLO PHILOSOPHY</h3>
    <p>Capital protection is the key to consistent profitability and equity growth. flexibility and taking advantage of opportunities when they arise.</p>
  </div>
  <div class="feature blue">
    <svg width="40" height="40" viewBox="0 0 40 40"><path d="M18 4h16v32H18" fill="none" stroke="#fff" stroke-width="4"/><path d="M4 20h20M17 13l7 7-7 7" fill="none" stroke="#fff" stroke-width="4"/></svg>
    <h3>TRADLO FREE TRIAL</h3>
    <p>Free forex signals for 30 days. trading signals to help you beat the forex market.</p>
  </div>
</section>

<section class="welcome-bg" role="img" aria-label="Faint photo of a hand with a pen over printed trading charts"></section>
<section class="welcome">
  <h2>Welcome to Tradlo</h2>
  <div class="tagline">MOMENTS MATTER MOST.&nbsp; RESHAPE YOUR PATH</div>
  <div class="tagline-2">FOREX SIGNAL SERVICES</div>
  <p>We use proven strategies to help traders in succeeding in the forex market. Our forex experts provide high-probability, professional and consistent forex signals and charts that help traders in maximizing their profits and eliminating losses.</p>
  <p>We use proven strategies to help traders in succeeding in the forex market. Our forex experts provide high-probability, professional and consistent forex signals and charts that help traders in maximizing their profits and eliminating losses.&nbsp; Try our free Currency&nbsp; Education service to find out what differentiates us from our competitors and how we can aid you in becoming a professional trader!</p>
  <h4>WHAT IS YOUR TRADING PHILOSOPHY AND STYLE?</h4>
  <p class="tight">We follow naked forex trading techniques including price action, immediate trend and personalized mathematical formulas. Our success stems from our strict enforcement of discipline, patience, attitude, economics and timing to help our traders maximize their gains from forex trading.&nbsp; Obviously we do not always win, but our winning trades exceed those that are not and our take profit target is always bigger than our stop loss. We look at multiple time frames to qualify setups that define our trading edge.&nbsp; We pay close to the London market and our entries are often based off of the 1-hour chart.</p>
</section>

<section class="plans-bg" role="img" aria-label="Blue tinted photo of financial charts and graphs"></section>
<section class="plans">
  <h2>Membership Plans</h2>
  <p>Disclaimer Trading foreign exchange ("Forex") on margin carries a high level of risk, and may not be suitable for all investors. Before deciding to trade Forex you should carefully consider your investment objectives, level of experience, and onlytrade with the money you are prepared to lose. The possibility exists that you could sustain a loss in excess of all of your deposited funds and therefore you should not speculate with capital that you cannot afford to lose. You should be aware of all the risks associated with foreign exchange.</p>
  <p>Clients must be at least 18 years old to use the services of TRADLO. You acknowledge that past performance is not an indicator of future returns and that references to performance on this Site are provided as historical benchmarks only. TRADLO does not take responsibility for loss incurred as a result of our trading signals. By signing up as a member you acknowledge that we are not providing financial advice and that you are making the decision to use ourtrades on your own account. All information provided by TRADLO, in any form, is for educational purposes only.</p>
</section>

<article class="plan" style="left:244px">
  <div class="plan-price">$ 58 USD</div><div class="plan-term">1 MONTH</div>
  <div class="plan-cta">Click here to<br>sign up for 1 month</div>
  <div class="plan-btn">ORDER NOW</div>
  <div class="pay-name">Paydex</div><div class="pay-btn"></div>
  <div class="pay-cards"><span></span><span></span><span></span><span></span><span></span></div>
</article>
<article class="plan" style="left:485px">
  <div class="plan-price">$ 145 USD</div><div class="plan-term">3 MONTH</div>
  <div class="plan-cta">Click here to<br>sign up for 1 month</div>
  <div class="plan-btn">ORDER NOW</div>
  <div class="pay-name">Paydex</div><div class="pay-btn"></div>
  <div class="pay-cards"><span></span><span></span><span></span><span></span><span></span></div>
</article>
<article class="plan" style="left:726px">
  <div class="plan-price">$ 450 USD</div><div class="plan-term">12 MONTH</div>
  <div class="plan-cta">Click here to<br>sign up for 1 month</div>
  <div class="plan-btn">ORDER NOW</div>
  <div class="pay-name">Paydex</div><div class="pay-btn"></div>
  <div class="pay-cards"><span></span><span></span><span></span><span></span><span></span></div>
</article>

<section class="faq-bg" role="img" aria-label="Pale photo of a hand holding a phone with digital graphics and a FOREX word"></section>
<h2 class="faq-title">FAQ</h2>
<div class="faq-open">
  <div class="q"><i>×</i>How many pips can I make per month following your signals?</div>
  <p>Our view is simple. Trading is a business and not for the faint of heart. We strive to achieve 150-250 real quality pips a month. More importantly, we're much more concerned with protecting our capital and minimizing our drawdown than we are with generating more pips under far more risky conditions. We stick to our strategy and keep losses small, because a steady edge grows accounts over time and patience pays off.</p>
</div>
<div class="faq-item" style="left:234px;top:1932px"><i>+</i>Can I follow your signals and have a full time job?</div>
<div class="faq-item" style="left:234px;top:1981px"><i>+</i>How will I receive my signals?</div>
<div class="faq-item" style="left:234px;top:2032px"><i>+</i>What happens after my trial period access?</div>
<div class="faq-item" style="left:624px;top:1800px"><i>+</i>How Will FOREX Signals Help You?</div>
<div class="faq-item" style="left:624px;top:1850px"><i>+</i>What we are not or should I say what we are?</div>
<div class="faq-item" style="left:624px;top:1900px"><i>+</i>How many pips can I make per month following your signals?</div>
<div class="faq-item" style="left:624px;top:1950px"><i>+</i>Don't need special requirements to earn money from my system?</div>
<div class="faq-item" style="left:624px;top:1999px"><i>+</i>Who do we serve?</div>
<div class="faq-item" style="left:624px;top:2050px"><i>+</i>How many pips can I make per month following your signals?</div>

<section class="contact-bg" role="img" aria-label="Dark photo of a businessman's hand touching a glowing network of icons"></section>
<h2 class="contact-title">CONTACT US</h2>
<div class="contact-rule"></div>
<p class="contact-intro">If you would like to get in contact with us, please fill in the form and we will get back to you as soon as we can.<br><br>Alternatively you can call us on</p>
<div class="contact-phone">0555 014 377</div>
<div class="stay">STAY CONNECTED</div>
<div class="social"><span style="background:var(--orange)"></span><span style="background:#3a5a9a"></span><span style="background:var(--blue-deep)"></span><span style="background:var(--sky)"></span></div>
<div class="field" style="left:492px;top:2254px;width:222px">Name</div>
<div class="field" style="left:744px;top:2254px;width:222px">Email</div>
<div class="field" style="left:492px;top:2316px;width:222px">Telephone</div>
<div class="field" style="left:744px;top:2316px;width:222px">Subject</div>
<div class="field" style="left:492px;top:2381px;width:474px;height:93px">Message</div>
<div class="remote"><div class="remote-brand"><span></span>LinkDesk</div><p>If requested by our staff to do so, please click on this link to start our <b>Remote Assistance Software</b>.</p></div>
<div class="send">SEND</div>
<nav class="footer-links">
  <span>HOME<br>FOREX RESOURCES</span><span>ABOUT US<br>WHY US?</span><span>MEMBERSHIP PLANS<br>OUR STRATEGY</span><span>PERFORMANCE<br>INVESTORS</span><span>FAQ<br>DISCLAIMER</span>
</nav>
<div class="bottom-bar"></div>
<p class="copyright">2017 © TRADLO ALL RIGHTS RESERVED.</p>
<div class="back-top">BACK TO TOP &nbsp;<svg width="10" height="7" viewBox="0 0 10 7"><path d="M1 6l4-4 4 4" fill="none" stroke="#fff" stroke-width="1.5"/></svg></div>

</body>
</html>
```